New business card for a regional office of a US M&A company

We need business card for a finance company, office based in Hong Kong , our Head office is in US, our business is to Merge and acquires companies , the new office will be a regional office for the Asia Pacific region. We want to use the head office logo as attached ( but don't have to be exactly the same, can be a variation to it) as a base and then add Asia Pacific alongside the logo.
We would prefer to have be bilingual Eng + Chinese, although we don't really have Chinese company name .

Industry/Entity Type

Business

Contact Information for Business Card

Clara Jo Tsang
 

VP,
APAC M&A Operations
Orin Vantage Asia Pacific Limited
 
Unit 1407, K18
18 Tai Lok Shan Road, 
Hong Kong 
 
M: +852 6038 1742
T : +852 2836 4100
F : +852 2836 4177
VOIP: 4158
 
cjtsang@orinvantage.com

Font styles to use
Serif
Sans Serif

Colors

Designer to choose colors to be used in the design.

Requirements
Must have
• APAC Office

```html
<!DOCTYPE html>
<html lang="en">
<head>
<meta charset="utf-8">
<title>Orin Vantage – Business Card</title>
<link rel="stylesheet" href="https://fonts.googleapis.com/css2?family=Roboto:wght@400;500;700&display=swap">
<style>
  :root {
    --backdrop: #e9e7e3;
    --navy: #0f2944;
    --sky: #1fabd0;
    --white: #ffffff;
    --muted: #c9d3dc;
    --shadow: rgba(0, 0, 0, 0.28);
  }
  html, body {
    margin: 0;
    width: 1200px;
    height: 960px;
    overflow: hidden;
    background: var(--backdrop);
    font-family: "Roboto", Arial, sans-serif;
  }
  .card {
    position: absolute;
    width: 600px;
    height: 343px;
    box-shadow: 0 3px 6px var(--shadow);
    overflow: hidden;
  }
  .card-front { left: 314px; top: 113px; background: var(--sky); }
  .card-back { left: 311px; top: 472px; background: var(--navy); }

  .brand-panel {
    position: absolute;
    left: 0; top: 0;
    width: 305px; height: 100%;
    background: var(--navy);
    border-right: 3px solid var(--white);
    display: flex;
    align-items: center;
    justify-content: center;
  }
  .brand-name {
    font-family: "Roboto", Arial, sans-serif;
    font-weight: 700;
    color: var(--sky);
    letter-spacing: 0.5px;
    white-space: nowrap;
    margin: 0;
  }
  .brand-panel .brand-name { font-size: 30px; margin-top: 60px; }

  .contact {
    position: absolute;
    left: 352px; top: 56px;
    color: var(--white);
    font-size: 14px;
    line-height: 18.5px;
  }
  .contact-name {
    margin: 0;
    font-size: 20px;
    font-weight: 700;
    line-height: 24px;
    letter-spacing: 0.2px;
  }
  .contact-role { margin: 2px 0 12px 2px; font-size: 14px; }
  .contact-address { margin: 0 0 8px; font-style: normal; }
  .contact-lines { list-style: none; margin: 0; padding: 0; }
  .contact-lines li { display: flex; align-items: center; gap: 9px; height: 19px; }
  .contact-lines svg { width: 14px; height: 14px; fill: var(--white); flex: none; }
  .contact-voip { margin: 10px 0 0; }

  .card-back .brand-name {
    position: absolute;
    left: 0; right: 0; top: 182px;
    text-align: center;
    font-size: 46px;
  }
  .web-address {
    position: absolute;
    left: 0; right: 0; top: 284px;
    text-align: center;
    color: var(--muted);
    font-size: 14px;
    letter-spacing: 6px;
    margin: 0;
  }
</style>
</head>
<body>

<section class="card card-front" aria-label="Business card front">
  <div class="brand-panel">
    <p class="brand-name">ORIN VANTAGE</p>
  </div>
  <div class="contact">
    <h1 class="contact-name">CLARA JO TSANG</h1>
    <p class="contact-role">VP</p>
    <address class="contact-address">
      APAC M&amp;A Operations<br>
      Orin Vantage Asia Pacific Limited<br>
      Unit 1407, K18<br>
      18 Tai Lok Shan Road<br>
      Hong Kong
    </address>
    <ul class="contact-lines">
      <li>
        <svg viewBox="0 0 24 24" aria-label="Telephone"><path d="M6.6 10.8c1.4 2.8 3.8 5.1 6.6 6.6l2.2-2.2c.3-.3.7-.4 1-.2 1.1.4 2.3.6 3.6.6.6 0 1 .4 1 1V20c0 .6-.4 1-1 1C10.6 21 3 13.4 3 4c0-.6.4-1 1-1h3.5c.6 0 1 .4 1 1 0 1.3.2 2.5.6 3.6.1.3 0 .7-.2 1l-2.3 2.2z"/></svg>
        +852 2836 4100
      </li>
      <li>
        <svg viewBox="0 0 24 24" aria-label="Mobile"><path d="M7 1h10a2 2 0 0 1 2 2v18a2 2 0 0 1-2 2H7a2 2 0 0 1-2-2V3a2 2 0 0 1 2-2zm0 3v14h10V4H7zm5 15.5a1 1 0 1 0 0 2 1 1 0 0 0 0-2z"/></svg>
        +852 6038 1742
      </li>
      <li>
        <svg viewBox="0 0 24 24" aria-label="Fax"><path d="M7 2h10v5H7zM3 8h18a1 1 0 0 1 1 1v8a1 1 0 0 1-1 1h-3v4H6v-4H3a1 1 0 0 1-1-1V9a1 1 0 0 1 1-1zm5 8v4h8v-4H8zm10-6v2h2v-2h-2z"/></svg>
        +852 2836 4177
      </li>
    </ul>
    <p class="contact-voip">VOIP: 4158</p>
  </div>
</section>

<section class="card card-back" aria-label="Business card back">
  <p class="brand-name">ORIN VANTAGE</p>
  <p class="web-address">www.orinvantage.com</p>
</section>

</body>
</html>
```